Brochure and Business Card design

I am looking for a high end, elegant A4, 4 page brochure booklet to convey our products to clientele that will be visiting a luxury display showroom.

Harrowgate Locks and Grilles is a Australian security provider, and we supply high end products from reputable brands.
The brochure will be directed to clients building a new home with a partnered building company and will be accompanied with display boards of our products.

I am providing files of a document we have put together with the relevant information and some images to help along the way, we are not bound by the layout or style it has been drawn up and we wish to give you complete creative freedom putting the peaces together. I have also provided the files for our logo in two different colours, and a picture of a brochure we love the look of.

If you have any suggestions, we can likely come up with further images etc if it will help or even if you feel some should be removed, we are open to that also

Target Market(s)

Young familys, people building new luxury homes, proffesionals, home owners

Industry/Entity Type

Business

Font styles to use
Serif
Sans Serif

Requirements
Must have
• All 8 pages
Should not have
• Not really a fan of reds and similar.

```html
<!DOCTYPE html>
<html lang="en">
<head>
<meta charset="utf-8">
<title>Ducted Vacuum – Brochure Spread</title>
<link rel="stylesheet" href="https://fonts.googleapis.com/css2?family=Questrial&family=Montserrat:wght@600;700&display=swap">
<style>
  :root {
    --board: #d3d3d3;
    --paper: #ffffff;
    --brand-blue: #1b84c6;
    --deep-blue: #1a5fae;
    --sky-blue: #2f9fde;
    --leaf-green: #8dbf1f;
    --body-grey: #5a5a5a;
    --heading-blue: #2a8ccf;
    --on-blue: #e8f3fb;
  }
  * { box-sizing: border-box; margin: 0; padding: 0; }
  html, body {
    width: 1200px; height: 645px; overflow: hidden;
    background: var(--board);
  }
  .spread {
    position: absolute; left: 0; top: 90px;
    width: 1253px; height: 485px;
    transform: scale(0.9577); transform-origin: 0 0;
    display: flex;
  }
  .page { position: relative; height: 485px; overflow: hidden; }

  /* Left page */
  .page--intro { width: 623px; background: var(--paper); }
  .family-photo {
    position: absolute; left: 0; top: 0; width: 623px; height: 330px;
    background: linear-gradient(120deg, #c7d3dc 0%, #e6d3c2 40%, #f0dccb 60%, #d9c3ad 100%);
  }
  .swoosh { position: absolute; left: 0; top: 0; width: 623px; height: 485px; }
  .accessories-photo {
    position: absolute; left: 13px; top: 216px; width: 186px; height: 236px;
    background: radial-gradient(ellipse at 50% 50%, #8c9094 0%, #c9ccce 55%, #ffffff 80%);
    border-radius: 8px;
  }
  .intro-title {
    position: absolute; left: 258px; top: 262px;
    font-family: "Questrial", sans-serif; font-weight: 400;
    font-size: 34px; line-height: 36px; color: var(--heading-blue);
  }
  .intro-copy {
    position: absolute; left: 261px; top: 344px; width: 348px;
    font-family: "Questrial", sans-serif; font-size: 9.2px; line-height: 15.5px;
    color: var(--body-grey); text-align: justify;
  }
  .intro-copy p + p { margin-top: 10px; }

  /* Right page */
  .page--features {
    width: 630px;
    background: linear-gradient(180deg, var(--deep-blue) 0%, var(--brand-blue) 55%, var(--sky-blue) 100%);
  }
  .unit-photo {
    position: absolute; left: 44px; top: 50px; width: 144px; height: 260px;
    background: linear-gradient(90deg, #3f4247 0%, #6a6e74 45%, #45484d 100%);
    border-radius: 14px 14px 6px 6px;
  }
  .feature-column { position: absolute; width: 170px; color: var(--on-blue); font-family: "Questrial", sans-serif; }
  .feature-column--left { left: 228px; }
  .feature-column--right { left: 416px; }
  .feature {
    position: absolute; left: 0; width: 170px;
  }
  .feature h2 {
    font-family: "Montserrat", sans-serif; font-weight: 700;
    font-size: 11px; line-height: 13px; color: #ffffff; margin-bottom: 5px;
  }
  .feature p { font-size: 7.6px; line-height: 10.4px; }
  .feature p + p { margin-top: 9px; }
  .feature strong { font-family: "Montserrat", sans-serif; font-weight: 700; }
</style>
</head>
<body>
  <div class="spread">
    <section class="page page--intro">
      <div class="family-photo" role="img" aria-label="Photograph of a smiling young family at home"></div>
      <svg class="swoosh" viewBox="0 0 623 485" aria-hidden="true">
        <path d="M0 150 C150 110 300 150 420 230 C500 283 570 300 623 300 L623 485 L0 485 Z" fill="var(--brand-blue)"/>
        <path d="M0 168 C150 130 300 170 420 245 C500 293 570 308 623 310 L623 485 L0 485 Z" fill="var(--leaf-green)"/>
        <path d="M0 200 C150 175 300 210 420 268 C500 305 570 325 623 330 L623 485 L0 485 Z" fill="var(--paper)"/>
      </svg>
      <div class="accessories-photo" role="img" aria-label="Ducted vacuum hose, wand, floor heads and wall bracket"></div>
      <h1 class="intro-title">Ducted<br>Vacuum</h1>
      <div class="intro-copy">
        <p>Ducted vacuums with Harrowgate Locks and Grilles are the perfect accessory for keeping you home as good as new. With various units ranging from the smaller 2Hp - 2 to 4 outlet unit for the smaller home up to the 4Hp – 5 to 8 outlet unit for larger two story homes and everything in between.</p>
        <p>Don’t get caught up wrestling with and dragging around a corded vacuum. Use a ducted system and all you’ll need to carry is the wand.</p>
      </div>
    </section>

    <section class="page page--features">
      <div class="unit-photo" role="img" aria-label="Coastline Vac ducted vacuum power unit"></div>

      <div class="feature-column feature-column--left">
        <article class="feature" style="top:55px">
          <h2>A Coastline Vac ducted vacuum improves your health</h2>
          <p>Every day we breathe in billions of polluting particles around the home. In fact, <strong>the average house collects 18kg of dust a year!</strong> Along with other allergens this can have a major impact on health, especially for asthma and allergy sufferers.</p>
          <p>While portable vacuum cleaners appear to clean a room, they in fact release dust, bacteria and allergens back into the air. Coastline Vac ducted vacuum systems remove all vacuumed dust particles, allergens and noxious odours, creating a healthier living environment</p>
        </article>
        <article class="feature" style="top:272px">
          <h2>Faster Easier Cleaning</h2>
          <p>Ducted vacuum systems are versatile enough to be used just about anywhere. Carpets, hard floors, curtains, skirtings, staircases, cars and verandas can all be cleaned with a ducted vacuum system – even the family pet (yes, we have actually tested this – results differ from pet to pet!).</p>
          <p>The longer hose and convenient inlet valves of a ducted vacuum help you to reach all parts of your house effortlessly. A Coastline Vac ducted vacuum will speed up and simplify how you clean your home, giving you more time for the important things in life – you and your family.</p>
        </article>
      </div>

      <div class="feature-column feature-column--right">
        <article class="feature" style="top:55px">
          <h2>More Powerful Suction</h2>
          <p>A Coastline Vac ducted vacuum system <strong>has</strong> up to five times more power than most conventional portable vacuum cleaners.</p>
          <p>The heavy duty long-life motors used in all Coastline Vac systems ensure hard to shift dust and dirt will be removed from your valuable carpets, soft furnishings and other floor coverings, both protecting them and prolonging their lives. The ducted vacuum system also works well on curtains.</p>
        </article>
        <article class="feature" style="top:213px">
          <h2>The Cost Effective Cleaning Solution</h2>
          <p>Did you know that most ducted vacuum systems cost roughly the same as a high quality portable vacuum cleaner? The differences are that ducted vacuum systems last considerably longer (up to four times in fact), are more robust and require less maintenance. It all adds up to a more cost effective investment. Coastline Vac ducted vacuum systems are a semi-permanent feature and an excellent selling point for your home. Why? They not only make cleaning a breeze, they are built to last. That combination will increase the value of your home – well in excess of the original purchase price! As a ducted vacuum system is a semi-permanent structure in your house, it is covered under building insurance.</p>
        </article>
      </div>
    </section>
  </div>
</body>
</html>
```